Business Card Design Project

Business card based on attached logo

Todd Merrick
Todd@lorvantest.com
877-514-9073 ext. 318
Www.LorvanTest.com

Industry/Entity Type

Business

```html
<!DOCTYPE html>
<html lang="en">
<head>
<meta charset="utf-8">
<title>LorvanTest Business Cards</title>
<link rel="stylesheet" href="https://fonts.googleapis.com/css2?family=Archivo+Black&family=Questrial&family=Michroma&display=swap">
<style>
  :root {
    --red: #ec1c24;
    --ink: #231f20;
    --white: #ffffff;
    --backdrop: #e9e6e3;
    --card-w: 505px;
    --card-h: 290px;
  }
  * { margin: 0; padding: 0; box-sizing: border-box; }
  html, body {
    width: 1200px;
    height: 715px;
    overflow: hidden;
    background: var(--backdrop);
  }
  .sheet {
    position: relative;
    width: 1200px;
    height: 715px;
  }
  .card {
    position: absolute;
    width: var(--card-w);
    height: var(--card-h);
    border-radius: 22px;
    overflow: hidden;
    box-shadow: 0 2px 6px rgba(0,0,0,0.25);
  }
  .card--contact { left: 54px;  top: 47px;  background: var(--white); }
  .card--white   { left: 625px; top: 40px;  background: var(--white); }
  .card--red     { left: 52px;  top: 380px; background: var(--red); }
  .card--black   { left: 629px; top: 383px; background: var(--ink); }

  .brand {
    font-family: "Archivo Black", sans-serif;
    font-weight: 400;
    letter-spacing: -1px;
    line-height: 1;
    white-space: nowrap;
  }
  .brand-mark {
    display: inline-block;
    background: var(--red);
  }

  /* Contact card */
  .card--contact .brand-row {
    position: absolute;
    left: 42px;
    top: 40px;
    display: flex;
    align-items: flex-start;
    gap: 6px;
  }
  .card--contact .brand { font-size: 44px; color: var(--ink); }
  .card--contact .brand-mark { width: 16px; height: 16px; margin-top: -6px; }

  .holder-name {
    position: absolute;
    left: 46px;
    top: 178px;
    font-family: "Michroma", sans-serif;
    font-size: 15px;
    font-weight: 400;
    letter-spacing: 2px;
    color: var(--red);
  }
  .contact-list {
    position: absolute;
    left: 46px;
    top: 212px;
    list-style: none;
    font-family: "Questrial", sans-serif;
    font-size: 13.5px;
    color: var(--ink);
  }
  .contact-list li {
    display: flex;
    align-items: center;
    gap: 6px;
    height: 22px;
  }
  .contact-list svg { width: 11px; height: 11px; fill: var(--red); }

  .url-band {
    position: absolute;
    left: 0;
    bottom: 0;
    width: 100%;
    height: 31px;
    background: var(--red);
  }
  .url-band .url {
    position: absolute;
    left: 46px;
    top: 8px;
    font-size: 12.5px;
    color: var(--white);
  }
  .corner-square {
    position: absolute;
    right: 52px;
    bottom: 8px;
    width: 72px;
    height: 72px;
    background: var(--red);
    border: 4px solid var(--white);
  }

  .url {
    font-family: "Questrial", sans-serif;
    letter-spacing: 3px;
    white-space: nowrap;
  }

  /* Logo-only cards */
  .logo-lockup {
    position: absolute;
    left: 0;
    top: 88px;
    width: 100%;
    display: flex;
    justify-content: center;
    align-items: flex-start;
    gap: 8px;
  }
  .logo-lockup .brand { font-size: 58px; }
  .logo-lockup .brand-mark { width: 22px; height: 22px; margin-top: -12px; }
  .logo-lockup--light .brand-mark { background: var(--white); }

  .card--white .brand { color: var(--ink); }
  .card--red .brand,
  .card--black .brand { color: var(--white); }

  .card-url {
    position: absolute;
    left: 0;
    bottom: 18px;
    width: 100%;
    text-align: center;
    font-size: 15px;
  }
  .card--white .card-url { color: var(--ink); }
  .card--red .card-url,
  .card--black .card-url { color: var(--white); }
</style>
</head>
<body>
<main class="sheet">

  <section class="card card--contact" aria-label="Business card front with contact details">
    <div class="brand-row">
      <span class="brand">LorvanTest</span>
      <span class="brand-mark"></span>
    </div>
    <p class="holder-name">Todd Merrick</p>
    <ul class="contact-list">
      <li>
        <svg viewBox="0 0 24 24" aria-hidden="true"><path d="M6.6 10.8a15.1 15.1 0 0 0 6.6 6.6l2.2-2.2a1 1 0 0 1 1-.25 11.4 11.4 0 0 0 3.6.57 1 1 0 0 1 1 1V20a1 1 0 0 1-1 1A17 17 0 0 1 3 4a1 1 0 0 1 1-1h3.5a1 1 0 0 1 1 1c0 1.25.2 2.45.57 3.6a1 1 0 0 1-.25 1z"/></svg>
        <span>877-514-9073 ext. 318</span>
      </li>
      <li>
        <svg viewBox="0 0 24 24" aria-hidden="true"><path d="M2 6h20v12H2z M2 6l10 7 10-7" /></svg>
        <span>Todd@lorvantest.com</span>
      </li>
    </ul>
    <div class="url-band">
      <span class="url">www.LorvanTest.com</span>
    </div>
    <div class="corner-square" aria-hidden="true"></div>
  </section>

  <section class="card card--white" aria-label="Business card back, white">
    <div class="logo-lockup">
      <span class="brand">LorvanTest</span>
      <span class="brand-mark"></span>
    </div>
    <p class="card-url url">www.LorvanTest.com</p>
  </section>

  <section class="card card--red" aria-label="Business card back, red">
    <div class="logo-lockup logo-lockup--light">
      <span class="brand">LorvanTest</span>
      <span class="brand-mark"></span>
    </div>
    <p class="card-url url">www.LorvanTest.com</p>
  </section>

  <section class="card card--black" aria-label="Business card back, black">
    <div class="logo-lockup logo-lockup--light">
      <span class="brand">LorvanTest</span>
      <span class="brand-mark"></span>
    </div>
    <p class="card-url url">www.LorvanTest.com</p>
  </section>

</main>
</body>
</html>
```